New business stationairy

I need paper with header and footer and business cards.
I am a Ltd Company and my main field of expertise is QA/QC inspection in the Oil and Gas Industry. I will need all contact detail inserted and a footer with registration number and bank details etc

```html
<!DOCTYPE html>
<html lang="en">
<head>
<meta charset="utf-8">
<title>Harcourt Verification Services Ltd – Stationery</title>
<link href="https://fonts.googleapis.com/css2?family=Michroma&family=Arimo:wght@700&family=Tinos:wght@400;700&display=swap" rel="stylesheet">
<style>
  :root {
    --brand-blue: #2a2de3;
    --brand-blue-deep: #1d1fcf;
    --rule-grey: #8a8ea6;
    --ink: #111111;
    --paper: #ffffff;
  }
  html, body {
    margin: 0;
    padding: 0;
    overflow: hidden;
    background: var(--paper);
  }
  .letterhead {
    position: relative;
    width: 947px;
    height: 1200px;
    overflow: hidden;
    background: var(--paper);
  }
  .letterhead-shapes {
    position: absolute;
    inset: 0;
  }
  .company-title {
    position: absolute;
    margin: 0;
    font-family: "Michroma", sans-serif;
    font-weight: 400;
    color: var(--brand-blue);
    white-space: nowrap;
  }
  .letterhead .company-title {
    left: 105px;
    top: 152px;
    font-size: 24px;
    letter-spacing: 1px;
  }
  .header-address,
  .header-contact {
    position: absolute;
    margin: 0;
    font-family: "Arimo", sans-serif;
    font-weight: 700;
    font-size: 13px;
    line-height: 1.2;
    color: var(--ink);
    font-style: normal;
  }
  .header-address { left: 95px; top: 218px; }
  .header-contact { left: 600px; top: 108px; }
  .footer-details {
    position: absolute;
    left: 150px;
    width: 720px;
    top: 1163px;
    margin: 0;
    text-align: center;
    font-family: "Michroma", sans-serif;
    font-size: 13px;
    letter-spacing: 1px;
    color: var(--brand-blue);
    white-space: nowrap;
  }

  .business-card {
    position: absolute;
    left: 105px;
    top: 330px;
    width: 740px;
    height: 430px;
    background: var(--paper);
  }
  .card-shapes {
    position: absolute;
    inset: 0;
  }
  .business-card .company-title {
    left: 0;
    right: 0;
    top: 62px;
    text-align: center;
    font-size: 22px;
    letter-spacing: 1px;
  }
  .card-person {
    position: absolute;
    left: 55px;
    top: 170px;
    width: 200px;
    text-align: center;
    font-family: "Tinos", serif;
    font-weight: 700;
  }
  .card-name { margin: 0; font-size: 25px; color: var(--brand-blue); }
  .card-role { margin: 4px 0 0; font-size: 24px; color: var(--ink); }
  .card-address {
    position: absolute;
    right: 50px;
    top: 128px;
    margin: 0;
    text-align: right;
    font-family: "Tinos", serif;
    font-style: normal;
    font-size: 22px;
    line-height: 1.15;
    color: var(--ink);
  }
  .card-contact {
    position: absolute;
    left: 0;
    right: 0;
    top: 328px;
    margin: 0;
    text-align: center;
    font-family: "Tinos", serif;
    font-size: 22px;
    line-height: 1.15;
    color: var(--ink);
  }
</style>
</head>
<body>
<main class="letterhead">
  <svg class="letterhead-shapes" width="947" height="1200" viewBox="0 0 947 1200" aria-hidden="true">
    <defs>
      <linearGradient id="edge-left" x1="0" y1="0" x2="1" y2="0">
        <stop offset="0" stop-color="var(--brand-blue-deep)"/>
        <stop offset="1" stop-color="#ffffff"/>
      </linearGradient>
      <linearGradient id="edge-left-wide" gradientUnits="userSpaceOnUse" x1="0" y1="0" x2="150" y2="0">
        <stop offset="0" stop-color="var(--brand-blue-deep)"/>
        <stop offset="1" stop-color="#ffffff"/>
      </linearGradient>
      <linearGradient id="edge-right" x1="1" y1="0" x2="0" y2="0">
        <stop offset="0" stop-color="var(--brand-blue-deep)"/>
        <stop offset="0.55" stop-color="var(--brand-blue)"/>
        <stop offset="1" stop-color="#ffffff"/>
      </linearGradient>
    </defs>
    <path class="header-rule" d="M40 325 Q460 302 862 300" stroke="var(--rule-grey)" stroke-width="2" fill="none"/>
    <line class="footer-rule" x1="150" y1="1148" x2="886" y2="1148" stroke="var(--rule-grey)" stroke-width="2"/>
    <path class="left-band" d="M0 0 H60 Q38 300 10 560 Q70 900 150 1200 H0 Z" fill="url(#edge-left-wide)"/>
    <path class="side-band" d="M820 0 H947 V1200 H885 Q930 620 820 0 Z" fill="url(#edge-right)"/>
  </svg>

  <h1 class="company-title">HARCOURT VERIFICATION SERVICES LTD</h1>
  <address class="header-address">The Willows<br>Mill Road<br>Ashcombe<br>Fernley Marsh<br>Wessex<br>AB12 3CD</address>
  <p class="header-contact">Email: miriam.h@examplemail.co.uk<br>mobile: 07700900123</p>

  <section class="business-card">
    <svg class="card-shapes" width="740" height="430" viewBox="0 0 740 430" aria-hidden="true">
      <defs>
        <linearGradient id="card-band" x1="0" y1="0" x2="1" y2="0">
          <stop offset="0" stop-color="var(--brand-blue-deep)"/>
          <stop offset="0.5" stop-color="#ffffff"/>
          <stop offset="1" stop-color="var(--brand-blue-deep)"/>
        </linearGradient>
      </defs>
      <path class="card-band-top" d="M0 0 H740 V45 Q370 -15 0 45 Z" fill="url(#card-band)"/>
      <path class="card-band-bottom" d="M0 385 Q370 445 740 385 V430 H0 Z" fill="url(#card-band)"/>
      <line class="card-rule" x1="40" y1="112" x2="700" y2="112" stroke="var(--brand-blue)" stroke-width="1.5"/>
      <line class="card-rule" x1="40" y1="305" x2="700" y2="305" stroke="var(--brand-blue)" stroke-width="1.5"/>
    </svg>
    <h2 class="company-title">HARCOURT VERIFICATION SERVICES LTD</h2>
    <div class="card-person">
      <p class="card-name">Miriam Harcourt</p>
      <p class="card-role">Director</p>
    </div>
    <address class="card-address">The Willows<br>Mill Road<br>Ashcombe<br>Fernley Marsh<br>Wessex<br>AB12 3CD</address>
    <p class="card-contact">Email: miriam.h@examplemail.co.uk<br>mobile: 07700900123</p>
  </section>

  <p class="footer-details">Company Registration Number : 1234567 | Bank Details: 12345678</p>
</main>
</body>
</html>
```